Business card for my new company (Accounting firm)

I need a business card for my new business Brightwell Advisory and Ledger SA. Our services are accounting, tax, audit and financial management. Our customers are small companies, start-ups and new companies. The final design has to show financial security, trust and growth. Please find our logo attached to the business card. Text for the business card: Brightwell Advisory and Ledger SA Tomas Varenholt Director and Founder Certified Accountant Tel. 022 418 57 34 tv@clairevalconseil.ch www.clairevalconseil.ch Rue des Vergières 27 1201 Geneva
Target Market(s)
Our customers are small companies, start-ups and new companies.
Industry/Entity Type
Finance And Accounting
Contact Information for Business Card
Claireval Conseil et Comptes SA
Tomas Varenholt
Directeur et Fondateur
Expert-comptable diplômé
Tél. 022 418 57 34
tv@clairevalconseil.ch
www.clairevalconseil.ch
Rue des Vergières 27
1201 Genève

```html
<!DOCTYPE html>
<html lang="fr">
<head>
<meta charset="utf-8">
<title>Claireval Conseil et Comptes SA – Carte de visite</title>
<link href="https://fonts.googleapis.com/css2?family=Montserrat:wght@500&family=Roboto:wght@300;400;700&display=swap" rel="stylesheet">
<style>
  :root{
    --backdrop:#e4e4e4;
    --blue-light:#2c9fd4;
    --blue-mid:#1f80b8;
    --blue-deep:#17689c;
    --paper:#efefef;
    --ink:#3a3a3a;
    --white:#ffffff;
    --white-soft:rgba(255,255,255,.85);
  }
  *{margin:0;padding:0;box-sizing:border-box}
  html,body{width:1200px;height:726px;overflow:hidden;background:var(--backdrop)}
  .sheet{position:relative;width:1200px;height:726px}
  .card{position:absolute;top:205px;width:530px;height:316px;overflow:hidden;box-shadow:0 8px 24px rgba(0,0,0,.18)}
  .card--front{left:50px;background:linear-gradient(135deg,var(--blue-light),var(--blue-deep));
    display:flex;flex-direction:column;align-items:center;justify-content:center;color:var(--white)}
  .wordmark{font-family:"Montserrat",sans-serif;font-weight:500;text-transform:uppercase;letter-spacing:.12em}
  .card--front .wordmark{font-size:24px;text-align:center;line-height:1.3}
  .front-web{font-family:"Roboto",sans-serif;font-weight:700;font-size:15px;margin-top:26px;letter-spacing:.02em}

  .card--back{left:620px;background:var(--paper)}
  .back-band{position:absolute;left:0;right:0;top:112px;height:158px;
    background:linear-gradient(90deg,var(--blue-mid),var(--blue-light))}
  .card--back .wordmark{position:absolute;left:28px;top:62px;font-size:21px;color:var(--ink)}
  .holder{position:absolute;left:28px;top:126px;color:var(--white);font-family:"Roboto",sans-serif}
  .holder-name{font-weight:700;font-size:19px}
  .holder-role{font-weight:300;font-size:12.5px;line-height:1.35;color:var(--white-soft);margin-top:3px}
  .contacts{list-style:none;margin-top:10px;font-weight:300;font-size:13px;line-height:1.45}
  .contacts li{display:flex;align-items:center;gap:8px}
  .contacts svg{width:12px;height:12px;fill:var(--white)}
  .address{position:absolute;left:28px;bottom:16px;font-family:"Roboto",sans-serif;font-size:13px;color:var(--ink)}
</style>
</head>
<body>
<main class="sheet">
  <section class="card card--front" aria-label="Recto">
    <p class="wordmark">Claireval<br>Conseil et Comptes</p>
    <p class="front-web">www.clairevalconseil.ch</p>
  </section>

  <section class="card card--back" aria-label="Verso">
    <div class="back-band"></div>
    <p class="wordmark">Claireval Conseil et Comptes</p>
    <div class="holder">
      <p class="holder-name">Tomas Varenholt</p>
      <p class="holder-role">Directeur et Fondateur<br>Expert-comptable diplômé</p>
      <ul class="contacts">
        <li><svg viewBox="0 0 24 24" aria-hidden="true"><path d="M6.6 10.8a15.1 15.1 0 0 0 6.6 6.6l2.2-2.2a1 1 0 0 1 1-.25 11.4 11.4 0 0 0 3.6.57 1 1 0 0 1 1 1V20a1 1 0 0 1-1 1A17 17 0 0 1 3 4a1 1 0 0 1 1-1h3.5a1 1 0 0 1 1 1c0 1.25.2 2.45.57 3.57a1 1 0 0 1-.25 1z"/></svg>022 418 57 34</li>
        <li><svg viewBox="0 0 24 24" aria-hidden="true"><path d="M2 5h20v14H2zm2 2v.5l8 5 8-5V7l-8 5z"/></svg>tv@clairevalconseil.ch</li>
        <li><svg viewBox="0 0 24 24" aria-hidden="true"><path d="M12 2a10 10 0 1 0 0 20 10 10 0 0 0 0-20zm6.9 9h-3a15 15 0 0 0-1.3-6A8 8 0 0 1 18.9 11zM12 4c.9 1.3 1.7 3.8 1.9 7h-3.8C10.3 7.8 11.1 5.3 12 4zM9.4 5a15 15 0 0 0-1.3 6h-3A8 8 0 0 1 9.4 5zM5.1 13h3a15 15 0 0 0 1.3 6 8 8 0 0 1-4.3-6zM12 20c-.9-1.3-1.7-3.8-1.9-7h3.8c-.2 3.2-1 5.7-1.9 7zm2.6-1a15 15 0 0 0 1.3-6h3a8 8 0 0 1-4.3 6z"/></svg>www.clairevalconseil.ch</li>
      </ul>
    </div>
    <p class="address">Rue des Vergières 27 1201 Genève</p>
  </section>
</main>
</body>
</html>
```